VELMOR Website Design

We need a website designed for our company VELMOR. We are a luxury lifestyle club that will provide benefits and services for our members. The site should be clean & sleek, preferably using black and white (or darker colors). (example sites: stravenhall.example, plinth.example)

Here is a link of a sample page I did using wix. (https://dunmere7.sitehostly.example/mysite) This can be used to get a general idea.

Target Market(s)

Upper Middle Class in the United States

Number of Pages Required

5+ page

Font styles to use
Sans Serif
Other font styles liked:
• Arial (or other similar fonts)

Requirements
Must have
• A clean design that is eye-catching and speaks to our company.
Nice to have
• Ideas for copy.

```html
<!DOCTYPE html>
<html lang="en">
<head>
<meta charset="utf-8">
<title>VELMOR — Members Only Lifestyle Club</title>
<link rel="stylesheet" href="https://fonts.googleapis.com/css2?family=Montserrat:wght@700&family=Open+Sans:wght@300;400&family=Roboto:wght@300;400&display=swap">
<style>
  :root {
    --navy: #0d0d80;
    --navy-deep: #0a0a6e;
    --ink: #1c1c1c;
    --white: #ffffff;
    --footer: #111112;
    --footer-text: #e6e6e6;
    --social-red: #e0101a;
    --social-orange: #e8430e;
    --social-sky: #1d8be0;
    --social-royal: #1b14c8;
  }
  * { box-sizing: border-box; margin: 0; padding: 0; }
  html, body { width: 1200px; height: 2571px; overflow: hidden; }
  body {
    position: relative;
    font-family: "Roboto", Arial, sans-serif;
    font-weight: 300;
    color: var(--ink);
    background: var(--white);
  }
  .page { position: relative; width: 1200px; height: 2571px; overflow: hidden; }

  /* Hero */
  .hero {
    position: absolute; left: 0; top: 0; width: 1200px; height: 657px;
    background:
      radial-gradient(ellipse at 30% 35%, rgba(240,170,140,.55), transparent 55%),
      radial-gradient(ellipse at 75% 45%, rgba(220,60,90,.5), transparent 55%),
      radial-gradient(ellipse at 20% 10%, rgba(110,80,200,.8), transparent 50%),
      linear-gradient(160deg, #3a2a8c 0%, #6a2a6a 45%, #8a2a3a 70%, #3a1a2a 100%);
  }
  .hero__bar { position: absolute; left: 0; top: 0; width: 1200px; height: 8px; background: var(--navy); }
  .brand {
    position: absolute; left: 63px; top: 0; width: 177px; height: 98px;
    background: var(--navy);
    display: flex; align-items: center; justify-content: center;
    font-family: "Open Sans", Arial, sans-serif; font-weight: 400;
    font-size: 33px; color: var(--white); letter-spacing: .5px;
  }
  .nav { position: absolute; top: 0; left: 0; width: 1200px; height: 98px; }
  .nav__item {
    position: absolute; top: 0; height: 98px;
    display: flex; align-items: center;
    font-family: "Roboto", Arial, sans-serif; font-weight: 300;
    font-size: 15px; color: var(--white);
  }
  .nav__item--active { background: var(--navy); justify-content: center; width: 72px; left: 571px; }
  .play {
    position: absolute; left: 560px; top: 289px; width: 80px; height: 80px;
  }

  /* Split sections */
  .photo { position: absolute; }
  .photo--party {
    left: 0; top: 657px; width: 600px; height: 534px;
    background:
      radial-gradient(ellipse at 40% 70%, rgba(255,140,70,.55), transparent 50%),
      linear-gradient(180deg, #7a6a8a 0%, #8a5a6a 50%, #3a2a30 100%);
  }
  .photo--stage {
    left: 600px; top: 1680px; width: 600px; height: 537px;
    background:
      radial-gradient(ellipse at 50% 40%, rgba(240,150,200,.6), transparent 55%),
      linear-gradient(180deg, #5a4ab8 0%, #9a4a9a 50%, #b03060 100%);
  }
  .section-title {
    position: absolute;
    font-family: "Montserrat", Arial, sans-serif; font-weight: 700;
    font-size: 52px; line-height: 1; color: var(--navy-deep);
    letter-spacing: -.5px;
  }
  .copy {
    position: absolute;
    font-size: 14.5px; line-height: 30px; color: var(--ink);
  }
  .btn-outline {
    position: absolute; width: 143px; height: 43px;
    border: 2px solid var(--navy-deep); border-radius: 22px;
    display: flex; align-items: center; justify-content: center;
    font-size: 15px; font-weight: 400; color: var(--navy-deep);
  }

  /* Benefits */
  .benefits {
    position: absolute; left: 0; top: 1191px; width: 1200px; height: 489px;
    background:
      linear-gradient(rgba(20,20,25,.55), rgba(20,20,25,.55)),
      linear-gradient(100deg, #4a4a4e 0%, #5e5e62 30%, #3a3a3e 60%, #6a6a6e 85%, #4a4a4e 100%);
  }
  .benefits__title {
    position: absolute; left: 0; top: 1282px; width: 1200px; text-align: center;
    font-family: "Montserrat", Arial, sans-serif; font-weight: 700;
    font-size: 52px; line-height: 1; color: var(--white);
  }
  .benefits__copy {
    position: absolute; left: 150px; top: 1366px; width: 900px; text-align: center;
    font-size: 14.5px; line-height: 34.3px; color: var(--white);
  }
  .btn-solid {
    position: absolute; left: 528px; top: 1538px; width: 143px; height: 44px;
    background: var(--navy); border-radius: 22px;
    display: flex; align-items: center; justify-content: center;
    font-size: 15px; font-weight: 400; color: var(--white);
  }

  /* Footer */
  .footer { position: absolute; left: 0; top: 2217px; width: 1200px; height: 354px; background: var(--footer); }
  .footer__brand {
    position: absolute; left: 0; top: 2270px; width: 1200px; text-align: center;
    font-family: "Open Sans", Arial, sans-serif; font-weight: 300;
    font-size: 31px; color: var(--white);
  }
  .social { position: absolute; left: 456px; top: 2337px; width: 290px; height: 44px; }
  .footer__nav { position: absolute; top: 2413px; left: 0; width: 1200px; height: 20px; }
  .footer__link {
    position: absolute; top: 0;
    font-size: 13px; font-weight: 300; color: var(--footer-text); letter-spacing: .3px;
  }
  .footer__legal {
    position: absolute; left: 0; top: 2511px; width: 1200px; text-align: center;
    font-size: 12px; font-weight: 300; color: var(--footer-text);
  }
</style>
</head>
<body>
<div class="page">

  <header class="hero" role="img" aria-label="Photo of friends laughing and toasting with champagne glasses under warm party lights">
  </header>
  <div class="hero__bar"></div>
  <div class="brand">VELMOR</div>
  <nav class="nav">
    <span class="nav__item nav__item--active">Home</span>
    <span class="nav__item" style="left:680px">About</span>
    <span class="nav__item" style="left:771px">Services and Benefits</span>
    <span class="nav__item" style="left:961px">Apply</span>
    <span class="nav__item" style="left:1050px">Contact</span>
  </nav>
  <svg class="play" viewBox="0 0 80 80" aria-label="Play video">
    <circle cx="40" cy="40" r="37" fill="none" stroke="#ffffff" stroke-width="3"/>
    <path d="M32 26 L56 40 L32 54 Z" fill="#ffffff"/>
  </svg>

  <section class="about">
    <div class="photo photo--party" role="img" aria-label="Photo of a group of friends toasting drinks on a waterfront terrace at dusk with string lights"></div>
    <h2 class="section-title" style="left:686px; top:748px">ABOUT VELMOR</h2>
    <p class="copy" style="left:686px; top:833px; width:420px">VELMOR is a members only lifestyle club founded in order to bring the best services, experiences, and opportunities to our diverse community of members.</p>
    <p class="copy" style="left:686px; top:954px; width:420px">Our members consist of creatives, athletes, artists, and other professionals.</p>
    <span class="btn-outline" style="left:686px; top:1051px">READ MORE</span>
  </section>

  <section class="benefits" role="img" aria-label="Photo of travellers stepping from a luxury car toward a private jet on the tarmac"></section>
  <h2 class="benefits__title">BENEFITS &amp; SERVICES</h2>
  <p class="benefits__copy">
    VELMOR membership provides you with amazing benefits and services.<br>
    Members receive access to the best accountants, attorneys, real estate agents, private bankers/advisers and more.<br>
    VELMOR members also receive access to private flight travel, premium luxury gym memberships, private social clubs, and<br>
    private investment opportunities
  </p>
  <span class="btn-solid">READ MORE</span>

  <section class="experiences">
    <h2 class="section-title" style="left:99px; top:1786px">EXPERIENCES</h2>
    <p class="copy" style="left:99px; top:1871px; width:400px">VELMOR organizes and supports a ton of private events and parties for our members. Members are also provided access to exclusive venues and events from our partners.</p>
    <p class="copy" style="left:99px; top:1991px; width:400px">Network with other members to build lasting relationships.</p>
    <span class="btn-outline" style="left:99px; top:2061px">READ MORE</span>
    <div class="photo photo--stage" role="img" aria-label="Photo of women singing and dancing with a microphone under colourful disco lights"></div>
  </section>

  <footer class="footer"></footer>
  <div class="footer__brand">VELMOR</div>
  <svg class="social" viewBox="0 0 290 44" aria-label="Social links">
    <circle cx="22" cy="22" r="22" fill="var(--social-red)"/>
    <circle cx="84" cy="22" r="22" fill="var(--social-orange)"/>
    <circle cx="144" cy="22" r="22" fill="var(--social-sky)"/>
    <circle cx="206" cy="22" r="22" fill="var(--social-royal)"/>
    <circle cx="267" cy="22" r="22" fill="var(--social-red)"/>
  </svg>
  <nav class="footer__nav">
    <span class="footer__link" style="left:346px">HOME</span>
    <span class="footer__link" style="left:429px">ABOUT</span>
    <span class="footer__link" style="left:516px">SERVICES AND BENEFITS</span>
    <span class="footer__link" style="left:710px">APPLY</span>
    <span class="footer__link" style="left:795px">CONTACT</span>
  </nav>
  <p class="footer__legal">Copyrights 2018velmor All Rights Reserved.</p>

</div>
</body>
</html>
```